Web Design Project

Brightfold Publishing owns and operates a large number of editorial websites. These websites provides mostly consumers in the financial services space with information and price comparisons for a particular service.

Brightfold Publishing, as the holding company for each of these sites, currently has no website. We need to build a website targeted towards potential partners for our websites. The idea being that when we start a conversation with a partner, they can view our site and obtain some basic information about who we are.

The structure of the site is to be very simple, containing only a brief description about who we are, our contact details and a list of some of our websites:
• CoverVault.net.au
• MotorPolicyCheck.com.au
• DwellingCoverCheck.com.au
• MedicalCoverCheck.com.au
• LegacyCoverCheck.com.au
• JourneyCoverCheck.com.au
• AnimalCoverCheck.com.au
• PrivateLendingCheck.com.au
• MobileCoolingUnit.com.au
• FixedSavingsYield.com.au
• ThriftyHousehold.com.au
• CoinNana.com.au
• TameYourPlastic.com.au
• PurseMinder.com.au
• ThirdPartyClaimsCoverNational.com.au
• Trade-Cover.com.au
• MotorPolicyProviders.com.au
• MedicalCoverProviders.com.au
• DwellingCoverHub.com
• LegacyCoverHub.com
• EarningsShieldCoverHub.com
• MedicalCoverHub.com
• AnimalCoverHub.com
• PrivateLendingHub.com
• ChargePlasticHub.com
• DwellingLendingHub.com
• RetireNestEgg.net.au

The design of the site should say 'Internet company', 'professional', 'fresh thinking'. The design should not look like a corporate site that you would see from any corporate services business with images of people in suits. We are ultimately an Internet business and there should be a unique feel to the site.

We are open to a suggestion of a colour pallet as the holding company does not have an established logo.

Some sites that we like are:

http://www.quillmarsh-studio.co.uk/#home
http://previewbox00.layoutdock.example/wt_52418/index.html
http://previewbox00.layoutdock.example/wordpress_61942/
http://ponderloop.example/
http://www.brindlux.example/
http://www.tobiasvrankel.example/
http://www.slickfrontdoors.example/Corporate/design-ideas-detail.html?id=4197
http://pairmint.example/
http://orvendal.example/

Reason: Hi all, Apologies, but I need to extend the timeline. One of our key stakeholders is away for the next week. There are a few good designs that we have received to date and there are some tweaks that we would like to see before making a final decision. Thank you to everyone that has submitted designs - Have a great new year. Derek

Reason: Sorry to have to delay the deadline on this, but we did not find anything in the designs really resonated with us. We will have a further think about the existing designs that have been submitted and how we can provide more specific feedback to the designers to make some modifications to the designs.

Target Market(s)

We are targeting insurance companies / brokers that we are talking to. The idea is that we show a professional face to them.

Industry/Entity Type

Financial

Requirements
Must have
• Home Page (possibly integrated with About us details)
Contact Us
Our Sites

```html
<!DOCTYPE html>
<html lang="en">
<head>
<meta charset="utf-8">
<title>Brightfold Publishing Pty Ltd</title>
<link href="https://fonts.googleapis.com/css2?family=Arimo:wght@400;700&display=swap" rel="stylesheet">
<style>
  :root{
    --bg-top:#dfe3ea;
    --bg-bottom:#8d97a8;
    --panel:#ffffff;
    --panel-edge:#7fd0cf;
    --footer-bg:#eef2ed;
    --brand-red:#c8262b;
    --band-red:rgba(196,34,38,0.88);
    --ink:#222;
    --muted:#9a9a9a;
    --teal:#1a9ab0;
    --rule:#cfd3cf;
    --nav-dark:#111;
    --arrow:rgba(120,126,118,0.75);
  }
  *{margin:0;padding:0;box-sizing:border-box}
  html,body{width:1104px;height:1200px;overflow:hidden}
  body{
    position:relative;
    font-family:"Arimo",Arial,sans-serif;
    color:var(--ink);
    background:linear-gradient(180deg,var(--bg-top) 0%,#bcc3cf 45%,var(--bg-bottom) 100%);
  }
  .abs{position:absolute}

  .brand{left:161px;top:62px}
  .brand-name{font-size:26px;color:var(--brand-red);letter-spacing:-1.6px;line-height:1;white-space:nowrap}
  .brand-tag{font-size:11px;color:#666;margin:4px 0 0 31px}
  .search{left:525px;top:75px;width:210px;height:24px;background:#fff;border:1px solid #d7d9dc;border-radius:2px}
  .search span{position:absolute;left:7px;top:6px;font-size:9.5px;color:#777}
  .search .go{position:absolute;right:2px;top:2px;width:20px;height:18px;background:var(--brand-red);border-radius:2px}
  .live{left:784px;top:75px;font-size:10.5px;color:#888}
  .social{display:flex;gap:4px}
  .social i{display:block;width:17px;height:17px;border-radius:2px}
  .s1{background:#6f7478}.s2{background:#2f6cc7}.s3{background:#1f78b5}.s4{background:#e66a17}
  .social-top{left:871px;top:72px}
  .support{left:784px;top:101px;font-size:10.5px;color:#888}
  .support b{font-weight:400;color:var(--teal)}

  .panel{left:140px;top:117px;width:841px;height:968px;background:var(--panel);border:1px solid var(--panel-edge)}
  .nav{left:156px;top:134px;display:flex;align-items:center;font-size:10px;letter-spacing:.2px}
  .nav a{color:#111;text-decoration:none}
  .nav .current{background:var(--nav-dark);color:#fff;width:68px;height:26px;line-height:26px;text-align:center;border-radius:2px;margin-right:18px}
  .nav a+a{margin-right:13px}

  .hero{left:149px;top:174px;width:823px;height:343px;overflow:hidden;
    background:linear-gradient(90deg,#e7e9dd 0%,#f4f4ef 55%,#e8ead9 100%)}
  .hero-band{position:absolute;left:0;bottom:0;width:100%;height:81px;background:var(--band-red)}
  .hero-title{position:absolute;left:34px;top:10px;font-size:24px;color:#fff;letter-spacing:-1.4px}
  .hero-sub{position:absolute;left:34px;top:40px;font-size:10px;color:#fbe0e0}
  .arrow{width:42px;height:42px;background:var(--arrow);border-radius:2px;top:327px}
  .arrow svg{display:block;margin:13px auto}

  h2{font-weight:400;font-size:15.5px;color:#333}
  .sub{font-size:8.5px;color:var(--muted)}
  .copy{font-size:10.5px;line-height:17px;color:#222}

  .welcome{left:169px;top:548px;width:462px}
  .welcome .sub{margin:6px 0 0 1px}
  .welcome .copy{margin:20px 0 0 1px}
  .welcome .copy p+p{margin-top:17px}
  .more{display:block;text-align:right;font-size:10.5px;font-weight:700;color:var(--teal);margin-top:5px}

  .whatwe{left:169px;top:738px;width:462px}
  .whatwe .sub{margin:6px 0 0 1px}
  .feature{position:absolute;top:61px;display:flex}
  .feature .ico{width:50px;height:50px;margin-right:14px}
  .feature p{width:150px}

  .sites{left:674px;top:548px;width:270px}
  .sites .sub{margin:6px 0 0 1px}
  .item{padding:17px 0 9px;border-bottom:1px solid var(--rule);width:260px}
  .item:last-child{border-bottom:0}
  .item .meta{font-size:8.5px;color:var(--muted)}
  .item .meta b{font-weight:400;color:var(--teal)}
  .item h3{font-size:10.5px;color:var(--teal);font-weight:700;margin:5px 0 2px}

  .foot{left:141px;top:889px;width:839px;height:195px;background:var(--footer-bg)}
  .fcol{top:914px;width:154px;font-size:9px;line-height:17px;color:#222}
  .fcol h4{font-size:11.5px;font-weight:700;color:#333;padding-bottom:5px;border-bottom:1px solid var(--rule);margin-bottom:7px;line-height:1.2}
  .fcol li{list-style:none;white-space:nowrap}
  .bullets li{padding-left:16px;position:relative}
  .bullets li::before{content:"»";position:absolute;left:0;color:#aaa;font-size:8px}
  .fcol b{font-weight:700}
  .contact{width:185px;line-height:12px}
  .contact h4{margin-bottom:10px}
  .contact p{margin-top:12px;white-space:nowrap}
  .contact p:first-of-type{margin-top:0}

  .legal{left:161px;top:1099px;font-size:10.5px;color:#fff}
  .social-bottom{left:836px;top:1099px;gap:7px}
  .social-bottom i{width:20px;height:20px}
</style>
</head>
<body>

<header>
  <div class="abs brand">
    <div class="brand-name">Brightfold Publishing Pty Ltd</div>
    <div class="brand-tag">online publishing company</div>
  </div>
  <div class="abs search"><span>Search</span><div class="go">
    <svg width="20" height="18" viewBox="0 0 20 18"><circle cx="9" cy="8" r="4" fill="none" stroke="#fff" stroke-width="1.8"/><line x1="12" y1="11" x2="15" y2="14" stroke="#fff" stroke-width="2"/></svg>
  </div></div>
  <div class="abs live">Click here to live</div>
  <div class="abs social social-top"><i class="s1"></i><i class="s2"></i><i class="s3"></i><i class="s4"></i></div>
  <div class="abs support">Support Tell Free <b>1-800-555-019</b></div>
</header>

<div class="abs panel"></div>

<nav class="abs nav">
  <a class="current">HOME</a>
  <a>ABOUT US</a>
  <a>SERVICES</a>
  <a>PORTFOLIO</a>
  <a style="margin-left:5px">CONTACT US</a>
</nav>

<section class="abs hero" role="img" aria-label="Banner illustration: giraffe carrying a red shopping bag beside a city skyline, birds on street lamps and stacked slogans about interface, motion design and branding">
  <div class="hero-band">
    <div class="hero-title">Brightfold Publishing Pty Ltd</div>
    <div class="hero-sub">Brightfold Publishing is an Australian-based online publishing company</div>
  </div>
</section>
<div class="abs arrow" style="left:165px"><svg width="10" height="16" viewBox="0 0 10 16"><polyline points="8,2 2,8 8,14" fill="none" stroke="#fff" stroke-width="2"/></svg></div>
<div class="abs arrow" style="left:914px"><svg width="10" height="16" viewBox="0 0 10 16"><polyline points="2,2 8,8 2,14" fill="none" stroke="#fff" stroke-width="2"/></svg></div>

<section class="abs welcome">
  <h2>Welcome to Our Website</h2>
  <div class="sub">Brightfold Publishing is an Australian-based online publishing company</div>
  <div class="copy">
    <p><b>Brightfold Publishing</b> owns and operates a large number of editorial websites. Our sites give consumers in the financial services space clear information and price comparisons for insurance, lending, savings and everyday money. We work with insurers and brokers to reach readers who are ready to compare.</p>
    <p>If you are interested in partnering with us on one or multiple of our sites, please contact us.</p>
  </div>
  <a class="more">Read More »</a>
</section>

<section class="abs whatwe">
  <h2>What We Do</h2>
  <div class="sub">Information and price comparisons for financial services</div>
  <div class="feature copy" style="left:2px">
    <svg class="ico" viewBox="0 0 50 50" aria-hidden="true">
      <rect x="4" y="4" width="34" height="40" rx="3" fill="#f2c53a"/>
      <rect x="4" y="4" width="34" height="8" rx="3" fill="#f7dc73"/>
      <rect x="27" y="26" width="6" height="20" fill="#3fa63a"/>
      <rect x="20" y="33" width="20" height="6" fill="#3fa63a"/>
    </svg>
    <p>Editorial guides that explain cover, loans and savings in plain terms.</p>
  </div>
  <div class="feature copy" style="left:236px">
    <svg class="ico" viewBox="0 0 50 50" aria-hidden="true">
      <circle cx="25" cy="24" r="22" fill="#2aa7c9"/>
      <circle cx="26" cy="13" r="3.5" fill="#fff"/>
      <rect x="22" y="20" width="7" height="17" rx="2" fill="#fff"/>
    </svg>
    <p>Price comparisons that send ready-to-buy readers to our partners.</p>
  </div>
</section>

<section class="abs sites">
  <h2>Our Sites</h2>
  <div class="sub">A selection of the editorial websites we operate</div>
  <div class="item">
    <div class="meta">Insurance | <b>3 sites</b></div>
    <h3>Cover comparison</h3>
    <p class="copy">CoverVault.net.au, MotorPolicyCheck.com.au, DwellingCoverCheck.com.au</p>
  </div>
  <div class="item">
    <div class="meta">Insurance | <b>4 sites</b></div>
    <h3>Cover hubs</h3>
    <p class="copy">DwellingCoverHub.com, LegacyCoverHub.com, EarningsShieldCoverHub.com, MedicalCoverHub.com</p>
  </div>
  <div class="item">
    <div class="meta">Business | <b>2 sites</b></div>
    <h3>Business cover</h3>
    <p class="copy">ThirdPartyClaimsCoverNational.com.au, Trade-Cover.com.au</p>
  </div>
</section>

<footer>
  <div class="abs foot"></div>
  <div class="abs fcol bullets" style="left:168px">
    <h4>Comparison Sites</h4>
    <ul>
      <li>MedicalCoverCheck.com.au</li>
      <li>LegacyCoverCheck.com.au</li>
      <li>JourneyCoverCheck.com.au</li>
      <li>AnimalCoverCheck.com.au</li>
      <li>MotorPolicyProviders.com.au</li>
      <li>MedicalCoverProviders.com.au</li>
    </ul>
  </div>
  <div class="abs fcol" style="left:393px">
    <h4>Lending Sites</h4>
    <ul>
      <li>PrivateLendingCheck.com.au</li>
      <li>PrivateLendingHub.com</li>
      <li>DwellingLendingHub.com</li>
      <li>ChargePlasticHub.com</li>
      <li>RetireNestEgg.net.au</li>
      <li>AnimalCoverHub.com</li>
    </ul>
  </div>
  <div class="abs fcol" style="left:587px">
    <h4>Money Sites</h4>
    <ul>
      <li>ThriftyHousehold.com.au</li>
      <li>CoinNana.com.au</li>
      <li>TameYourPlastic.com.au</li>
      <li>PurseMinder.com.au</li>
      <li>MobileCoolingUnit.com.au</li>
      <li>FixedSavingsYield.com.au</li>
    </ul>
  </div>
  <div class="abs fcol contact" style="left:789px">
    <h4>Contact</h4>
    <p><b>Brightfold Publishing Pty Ltd</b></p>
    <p><b>Suite 412<br>18 Harbourline Road<br>Kestrel Bay NSW&nbsp;&nbsp;&nbsp; 2099</b></p>
    <p><b>Tel: 02 9555 0147</b></p>
    <p><b>Email: info@brightfold.example</b></p>
  </div>

  <div class="abs legal">© Copyright&nbsp; Brightfold Publishing Pty Ltd . All Rights Reserved&nbsp;&nbsp; |&nbsp;&nbsp;&nbsp; Home | Contact | RSS</div>
  <div class="abs social social-bottom"><i class="s1"></i><i class="s2"></i><i class="s3"></i><i class="s4"></i></div>
</footer>

</body>
</html>
```